Norrell Advisory WA Business Card

Create an interesting, eye catching and colourful two sided business card. We are a business consulting operation assisting SME's improve all areas of their business. We provide consulting services to assist SME's to create a culture of continuous improvement, making a positive difference in the business. Our tag line is Small changes, big rewards. We want to create a well recognised, innovative brand that can be continued throughout our website, social media and email correspondence.

Target Market(s)

Small to Medium Enterprise Business Owners

Industry/Entity Type

Business Consultant

Contact Information for Business Card

Name of Business: Norrell Advisory - Small Changes Big Rewards
Derek Holloway Ph 0407385510 Megan Holloway Ph 0407913847
Email norrelladvisorywa@mailbox-example.com
Web address TBA
FaceBook page TBA

BACKSIDE OF CARD

Providing assistance with:

• Organisation & Efficiency
• Revenue generation & Marketing
• Financial Management
• Production quality & delivery
• Systems & Process documentation
• Exit Strategy

Font styles to use
Other font styles liked:
• Calibri

Colors

Designer to choose colors to be used in the design.

Requirements
Must have
• Calibri font

```html
<!DOCTYPE html>
<html lang="en">
<head>
<meta charset="utf-8">
<title>Norrell Advisory WA Business Card</title>
<link href="https://fonts.googleapis.com/css2?family=Open+Sans:wght@400;600;700&display=swap" rel="stylesheet">
<style>
  :root {
    --backdrop: #5a5b5e;
    --card: #ffffff;
    --brand-red: #e8402f;
    --brand-blue: #0a72b5;
    --ink: #1d1d1f;
    --band-text: #ffffff;
  }
  * { margin: 0; padding: 0; box-sizing: border-box; }
  html, body { width: 1200px; height: 1000px; overflow: hidden; }
  body {
    background: var(--backdrop);
    font-family: "Open Sans", Calibri, sans-serif;
    position: relative;
  }
  .card {
    position: absolute;
    left: 240px;
    width: 720px;
    height: 410px;
    background: var(--card);
    border-radius: 28px;
    overflow: hidden;
  }
  .card--back { top: 50px; }
  .card--front { top: 540px; }

  /* back side */
  .back-brand {
    position: absolute; top: 120px; left: 0; right: 0;
    display: flex; justify-content: center; align-items: center; gap: 14px;
  }
  .brand-mark { width: 30px; height: 30px; background: var(--brand-red); }
  .brand-name {
    color: var(--brand-red); font-weight: 700; font-size: 34px; letter-spacing: 0.5px;
  }
  .back-tagline {
    position: absolute; top: 235px; left: 0; right: 0; text-align: center;
    color: var(--brand-blue); font-weight: 700; font-size: 19px;
  }
  .services {
    position: absolute; top: 270px; left: 0; right: 0; text-align: center;
    color: var(--ink); font-weight: 600; font-size: 16.5px; line-height: 25px;
  }

  /* front side */
  .front-brand {
    position: absolute; left: 40px; top: 150px; width: 270px;
    display: flex; align-items: center; gap: 10px;
  }
  .front-brand .brand-mark { width: 22px; height: 22px; flex: none; }
  .front-brand .brand-name { font-size: 23px; white-space: nowrap; }
  .divider {
    position: absolute; left: 322px; top: 40px; width: 2px; height: 260px;
    background: var(--ink);
  }
  .contacts { position: absolute; left: 345px; top: 44px; }
  .person-name {
    color: var(--brand-blue); font-weight: 700; font-size: 24px; line-height: 26px;
  }
  .person-phone {
    color: var(--ink); font-size: 24px; line-height: 28px; margin-bottom: 4px;
  }
  .contact-list { list-style: none; margin-top: 18px; }
  .contact-list li {
    display: flex; align-items: center; gap: 10px;
    color: var(--ink); font-size: 18px; line-height: 28px;
  }
  .contact-list svg { width: 16px; height: 16px; flex: none; }
  .band {
    position: absolute; left: 0; right: 0; bottom: 0; height: 82px;
    background: var(--brand-blue);
    display: flex; align-items: center; justify-content: center;
  }
  .band-tagline {
    color: var(--band-text); font-size: 19px; letter-spacing: 1px; margin-left: -120px;
  }
</style>
</head>
<body>

<section class="card card--back">
  <div class="back-brand">
    <span class="brand-mark"></span>
    <span class="brand-name">NORRELL ADVISORY</span>
  </div>
  <p class="back-tagline">CREATING A CULTURE OF CONTINUOUS IMPROVEMENT</p>
  <p class="services">
    Organisation &amp; Efficiency | Revenue generation &amp; Marketing | Financial Management<br>
    Production quality &amp; delivery | Systems &amp; Process documentation | Exit Strategy
  </p>
</section>

<section class="card card--front">
  <div class="front-brand">
    <span class="brand-mark"></span>
    <span class="brand-name">NORRELL ADVISORY</span>
  </div>
  <div class="divider"></div>
  <div class="contacts">
    <p class="person-name">DEREK HOLLOWAY</p>
    <p class="person-phone">0407385510</p>
    <p class="person-name">MEGAN HOLLOWAY</p>
    <p class="person-phone">0407913847</p>
    <ul class="contact-list">
      <li>
        <svg viewBox="0 0 16 16" aria-hidden="true"><rect x="1" y="3" width="14" height="10" rx="1.5" fill="#0a72b5"/><path d="M1.5 4 L8 9 L14.5 4" fill="none" stroke="#fff" stroke-width="1.4"/></svg>
        norrelladvisorywa@mailbox-example.com
      </li>
      <li>
        <svg viewBox="0 0 16 16" aria-hidden="true"><circle cx="8" cy="8" r="6.5" fill="none" stroke="#0a72b5" stroke-width="1.5"/><ellipse cx="8" cy="8" rx="2.8" ry="6.5" fill="none" stroke="#0a72b5" stroke-width="1.2"/><line x1="1.5" y1="8" x2="14.5" y2="8" stroke="#0a72b5" stroke-width="1.2"/></svg>
        www.norrelladvisory-example.com
      </li>
      <li>
        <svg viewBox="0 0 16 16" aria-hidden="true"><circle cx="8" cy="8" r="6" fill="#0a72b5"/></svg>
        norrelladvisory
      </li>
    </ul>
  </div>
  <div class="band">
    <p class="band-tagline">SMALL CHANGES * BIG REWARDS</p>
  </div>
</section>

</body>
</html>
```